Tradlo - Forex Signal Services Moments Matter Most. Reshape your path.

I need an attractive eye catching web design that is azure friendly. I currently have a web programmer working on the backend of my website. Now I need a professional design to attract and retain customers. This site needs to be mobile friendly.

Tradlo is a highly reputable, trustworthy and professional site that offers forex signals to traders in all parts of the globe. With accurate and reliable forex signals, traders can not only make money but also boost their profits.

At Tradlo, we want our clients to have complete faith on us and our services! We also do not want our users to lead a simple and monotonous life. Instead our goal is to help them create an extra source of steady income. However, this is possible only when our clients resolve to change their lives for the better. They need to change their mindset and most importantly develop a positive frame of mind. That’s exactly why at Tradlo, we provide our clients with innumerable personal development tools and resources that’ll aid them in changing all the aspects of their lives. We want our traders to feel inspired and educate them in the right way!

Colors are flexible.

I do like the simplicity of www.brightmarkvo.example.
I do want a design more professional in appearance and not everything on page one.

I have not been able to decide on a logo. There is one of lower quality as I have not paid for it yet but I will if you decide it's the best for my business I will. Or should one feel that they have a better idea for a logo, I will pay for it if i like it.

I have included some of the content of my site so you can get a feel for where I am coming from.
(Please note that this content is still in the editing process)
Updates

Project Deadline Extended Reason: My content was not complete nor finalization of the final logo. We will allow a few more days for designers to modify the website.Thank you for your patience and understanding. Added Tuesday, January 24, 2017

Target Market(s)

I work with Forex Traders, Investors wanting to control their own portfolios, and remote nomads/mellienials

Coding

Coded - Design and coding required

Number of Pages Required

5+ page

Requirements
Must have
• I must have a professional clean look. I want the site to be interactive and eye catching. I want my audience hooked within seconds of opening it. It has to have all important information first. Photos must be legit and not spammy. I work as a representative in the financial market. I want my site to reflect that I stand by my product and reputation means everything to me. This site has to be engaging.
• Sorry, I should have included this earlier of what I will all need on this site.
• I'll have about Tradlo (my company, what we stand for, who we work with, my strategy, etc....
• about me (why i started this company, who I am)
• Performance (graphs and recent posts of signals)
• Membership (how to sign up)
• Terms of service/legal/disclaimers
• FAQS
• Personal Development Resources
• Forex Education Resources
Nice to have
• Quick links to bounce around the site faster.
Should not have
• I do not want over the top white collar conservative.

```html
<!DOCTYPE html>
<html lang="en">
<head>
<meta charset="utf-8">
<title>Tradlo - Forex Signal Services Moments Matter Most. Reshape your path.</title>
<link rel="stylesheet" href="https://fonts.googleapis.com/css2?family=Open+Sans:ital,wght@0,400;0,600;0,700;0,800;1,800&display=swap">
<style>
:root{
  --green:#7c9d4c;
  --green-light:#9dbb68;
  --green-dark:#4e6a2c;
  --green-deep:#3b5222;
  --ink:#2e2e2e;
  --grey:#666;
  --line:#d8d8d8;
  --paper:#ffffff;
  --mist:#efefef;
  --slate:#3c3f42;
  --night:#1d2022;
}
*{box-sizing:border-box;margin:0;padding:0}
html,body{width:1200px;height:4800px;overflow:hidden}
body{font-family:"Open Sans",Arial,sans-serif;color:var(--ink);background:var(--paper);font-size:14px;line-height:1.5}
.section-title{font-size:24px;font-weight:700;letter-spacing:1px;text-align:center;display:flex;align-items:center;justify-content:center;gap:22px}
.section-title::before,.section-title::after{content:"";width:70px;height:1px;background:var(--line)}
.section-title .accent{color:var(--green)}
.section-title.on-dark{color:#fff;position:relative}
.section-title.on-dark::before,.section-title.on-dark::after{background:rgba(255,255,255,.5)}

/* top bar */
.topbar{height:38px;background:#f4f4f4;display:flex;justify-content:flex-end;align-items:center;gap:26px;padding-right:40px;font-size:13px;color:var(--green-dark)}
.topbar .contact-item{display:flex;align-items:center;gap:6px}
.topbar .socials{display:flex;gap:6px}
.topbar .socials span{width:18px;height:18px;border-radius:50%;background:var(--green)}

/* header */
.site-header{height:90px;display:flex;align-items:center;justify-content:space-between;background:linear-gradient(90deg,#3a4042,#5d6468 40%,#8b9296)}
.brand{display:flex;align-items:center;gap:12px;padding-left:50px;font-size:40px;font-weight:700;color:var(--green-light)}
.brand .dot{width:16px;height:16px;border-radius:50%;background:var(--green-light)}
.main-nav{display:flex;height:100%;font-size:13px;font-weight:700;color:#fff}
.main-nav a{display:flex;align-items:center;padding:0 16px;color:inherit;text-decoration:none}
.main-nav a.active{background:var(--green)}

/* hero */
.hero{height:480px;position:relative;display:flex;flex-direction:column;align-items:center;justify-content:center;color:#fff}
.hero .hero-art{position:absolute;inset:0;background:radial-gradient(ellipse at 55% 45%,#8a8f92 0%,#5a5f63 40%,#2a2d30 100%)}
.hero h1{position:relative;font-size:40px;font-weight:700;line-height:1.2;text-align:center;text-transform:uppercase;letter-spacing:1px}
.hero .hero-brand{position:relative;margin-top:30px;font-size:64px;font-weight:700;color:var(--green-light)}
.hero .arrow{position:absolute;top:215px;width:40px;height:50px;background:rgba(255,255,255,.85);display:flex;align-items:center;justify-content:center}
.hero .arrow.prev{left:0}.hero .arrow.next{right:0}
.hero .dots{position:absolute;bottom:26px;display:flex;gap:8px}
.hero .dots span{width:24px;height:4px;background:rgba(255,255,255,.5)}
.hero .dots span:first-child{background:#fff}

/* welcome */
.welcome{height:144px;display:flex}
.welcome .welcome-title{flex:0 0 560px;background:var(--mist);display:flex;align-items:center;padding-left:50px;font-size:40px;font-weight:800;color:var(--slate)}
.welcome p{flex:1;background:var(--slate);color:#fff;display:flex;align-items:center;padding:0 50px 0 30px;font-size:15px;font-weight:600;line-height:1.6}

/* what we do */
.what-we-do{height:496px;padding-top:60px;border-bottom:1px solid var(--line)}
.services{display:flex;justify-content:center;gap:30px;margin-top:50px}
.service{width:250px;text-align:center}
.service .icon{width:120px;height:120px;margin:0 auto 18px;border-radius:50%;background:var(--green);border:6px solid var(--green-dark);display:flex;align-items:center;justify-content:center}
.service:nth-child(even){margin-top:40px}
.service h3{font-size:15px;font-weight:700}
.service p{font-size:14px;color:var(--grey);line-height:1.5}

/* strategy */
.strategy{height:536px;padding:64px 110px 0}
.strategy p{font-size:14px;color:#444;margin-top:26px;line-height:1.7}
.strategy .section-title + p{margin-top:48px}
.btn{display:inline-block;background:var(--green);color:#fff;font-weight:700;font-size:16px;border-radius:8px;padding:12px 30px}
.strategy .cta{text-align:center;margin-top:34px}

/* why */
.why{height:740px;position:relative;background:linear-gradient(180deg,#6f8f48,#86a85a 50%,#6c8c45);color:#fff;padding-top:44px}
.why .why-art{position:absolute;left:365px;top:170px;width:470px;height:470px;border-radius:50%;background:radial-gradient(circle,#2a2f33 0%,#2a2f33 58%,#4f6d2f 60%,#5b7a37 100%)}
.why .point{position:absolute;width:250px;font-size:15px;font-weight:700;line-height:1.45}
.why .point.center{text-align:center;width:300px;left:450px}
.why .point.left{text-align:right}

/* performance */
.performance{height:590px;padding-top:50px}
.year-select{width:240px;margin:24px auto 0;border:1px solid #bbb;border-radius:6px;height:38px;display:flex;align-items:center;justify-content:space-between;padding:0 16px;font-weight:700}
.tables{display:flex;justify-content:center;margin-top:30px}
.pips-table{width:470px;border-collapse:collapse;font-size:16px}
.pips-table th{background:var(--green);color:#fff;height:46px;font-weight:700;border:1px solid #fff}
.pips-table th:last-child{background:var(--green-dark)}
.pips-table td{height:50px;border:1px solid var(--line);text-align:center;font-weight:700;width:50%}
.pips-table tr:nth-child(even) td{background:#f5f5f5}

/* membership */
.membership{height:570px;position:relative;padding-top:56px}
.membership .membership-art{position:absolute;inset:0;background:linear-gradient(180deg,#5f7f3b,#7d9e50 50%,#5b7a37)}
.plans{position:relative;display:flex;justify-content:center;gap:50px;margin-top:34px}
.plan{width:240px;background:var(--night);border:4px solid var(--green-light);color:#fff;text-align:center}
.plan .price{font-size:54px;font-weight:800;font-style:italic;line-height:1.2;padding-top:14px}
.plan .period{font-size:14px;font-weight:700;padding:6px 0 16px;border-bottom:1px solid #444}
.plan ul{list-style:none;font-size:13px;color:#ccc}
.plan li{height:38px;line-height:38px;border-bottom:1px solid #333}
.plan li:nth-child(odd){background:#2a2e30}
.plan .order{margin:18px auto;width:150px;background:var(--green);font-weight:800;font-style:italic;font-size:17px;padding:6px 0}

/* faq */
.faq{height:360px;padding:56px 120px 0}
.faq h2{font-size:24px;font-weight:800;text-align:center;letter-spacing:.5px}
.faq h2 span{color:var(--green)}
.faq-grid{display:grid;grid-template-columns:1fr 1fr;column-gap:40px;margin-top:36px}
.faq-grid div{border-bottom:1px solid var(--line);padding:9px 0;font-size:14px;font-weight:600}

/* contact */
.contact{height:390px;background:var(--mist);display:flex;padding:50px 80px 0;gap:60px}
.contact h2{font-size:24px;font-weight:800;text-align:center;margin-bottom:30px}
.contact h2 span{color:var(--green)}
.message-form{flex:0 0 680px}
.form-grid{display:grid;grid-template-columns:1fr 1fr;gap:12px}
.field{background:#fff;border:1px solid #ccc;height:46px;padding:12px;font-size:13px;font-weight:600}
.field.message{grid-column:1/3;height:110px}
.contact-info ul{list-style:none;font-size:14px}
.contact-info li{display:flex;gap:14px;margin-bottom:22px;align-items:flex-start}
.contact-info .bullet{width:26px;height:26px;border-radius:50%;background:var(--green);flex:none}

/* trial */
.trial{height:150px;background:var(--green);display:flex;align-items:center;padding:0 80px;gap:28px;color:#fff}
.trial .seal{width:96px;height:96px;border-radius:50%;background:var(--green-dark);border:4px solid #fff;flex:none}
.trial p{font-size:23px;font-weight:700;flex:1;white-space:nowrap}
.trial .btn-trial{background:var(--slate);font-size:22px;font-weight:800;padding:16px 30px;white-space:nowrap}

/* disclaimer */
.disclaimer{height:174px;padding:20px 40px;font-size:12px;color:#444;line-height:1.55}

/* footer */
.site-footer{height:42px;background:var(--green-deep);color:#fff;display:flex;justify-content:space-between;align-items:center;padding:0 40px;font-size:12px;font-weight:600}
.site-footer nav{display:flex;gap:18px}
</style>
</head>
<body>

<div class="topbar">
  <span class="contact-item">
    <svg width="14" height="14" viewBox="0 0 24 24"><path d="M6 2l4 4-2 3c1.5 3 4 5.5 7 7l3-2 4 4-3 4C10 21 3 14 2 5z" fill="#4e6a2c"/></svg>
    (800) 555-0142
  </span>
  <span class="socials"><span></span><span></span><span></span><span></span></span>
  <span class="contact-item">
    <svg width="16" height="12" viewBox="0 0 16 12"><rect x=".5" y=".5" width="15" height="11" fill="none" stroke="#4e6a2c"/><path d="M.5.5l7.5 6 7.5-6" fill="none" stroke="#4e6a2c"/></svg>
    info@tradlo.example
  </span>
</div>

<header class="site-header">
  <div class="brand"><span class="dot"></span>Tradlo</div>
  <nav class="main-nav">
    <a class="active">HOME</a><a>WHAT WE DO</a><a>OUR STRATEGY</a><a>WHY TRADLO</a><a>PERFORMANCE</a><a>MEMBERSHIP</a><a>FAQs</a><a>CONTACT</a>
  </nav>
</header>

<section class="hero">
  <div class="hero-art" role="img" aria-label="Hand reaching toward a glowing world of currency symbols"></div>
  <h1>Moments Matter Most,<br>Reshape Your Path</h1>
  <div class="hero-brand">Tradlo</div>
  <span class="arrow prev"><svg width="14" height="20"><path d="M12 2L3 10l9 8" fill="none" stroke="#333" stroke-width="3"/></svg></span>
  <span class="arrow next"><svg width="14" height="20"><path d="M2 2l9 8-9 8" fill="none" stroke="#333" stroke-width="3"/></svg></span>
  <div class="dots"><span></span><span></span><span></span><span></span></div>
</section>

<section class="welcome">
  <h2 class="welcome-title">WELCOME TO TRADLO</h2>
  <p>We use proven strategies to help traders in succeeding in the forex market. Our forex experts provide high-probability, professional and consistent forex signals and charts that help traders in maximizing their profits and eliminating losses.</p>
</section>

<section class="what-we-do">
  <h2 class="section-title">WHAT <span class="accent">WE DO</span></h2>
  <div class="services">
    <div class="service">
      <div class="icon"><svg width="56" height="56" viewBox="0 0 56 56"><circle cx="28" cy="28" r="24" fill="none" stroke="#fff" stroke-width="3"/><path d="M14 28h28M28 14v28" stroke="#fff" stroke-width="3"/></svg></div>
      <h3>We Choose the Best Forex Pair</h3>
      <p>We use the only the best – 5 currency pairs</p>
    </div>
    <div class="service">
      <div class="icon"><svg width="60" height="50" viewBox="0 0 60 50"><rect x="3" y="3" width="54" height="36" fill="none" stroke="#fff" stroke-width="3"/><path d="M10 30l12-12 10 8 16-14" fill="none" stroke="#fff" stroke-width="3"/><path d="M22 46h16" stroke="#fff" stroke-width="3"/></svg></div>
      <h3>Analyze the Forex Chart</h3>
      <p>The Tradlo strategy is used to analyze all 5 chosen currency pair charts and the most profitable entry point is identified and sent to subscribers. Accurate and profitable entry points are not easy to find.</p>
    </div>
    <div class="service">
      <div class="icon"><svg width="50" height="56" viewBox="0 0 50 56"><path d="M6 3h28l10 10v40H6z" fill="none" stroke="#fff" stroke-width="3"/><path d="M14 34l8-8 6 6 10-10" fill="none" stroke="#fff" stroke-width="3"/></svg></div>
      <h3>Send Forex Signals</h3>
      <p>Signals are sent to our Subscribers through SMS, Members Area, Email and App push notification.</p>
    </div>
    <div class="service">
      <div class="icon"><svg width="56" height="56" viewBox="0 0 56 56"><circle cx="28" cy="28" r="22" fill="none" stroke="#fff" stroke-width="3"/><text x="28" y="38" text-anchor="middle" font-family="Open Sans,Arial,sans-serif" font-size="28" font-weight="700" fill="#fff">$</text></svg></div>
      <h3>You Make Money</h3>
      <p>150-250+ pips per month! A maximum of 15 to 30 signals is sent per month. Expect to make 10-50 pips per signal.</p>
    </div>
  </div>
</section>

<section class="strategy">
  <h2 class="section-title">OUR <span class="accent">STRATEGY</span></h2>
  <p>Tradlo.com works with both day as well as intraday traders. We only hold a maximum of one position at any given point in time. Once we've placed an order we do not move SL or TP targets.</p>
  <p>We follow naked forex trading techniques including price action, immediate trend and personalized mathematical formulas. Our success stems from our strict enforcement of discipline, patience, attitude, economics and timing to help our traders maximize their gains from forex trading. (please edit) At Tradlo, we trade GBP/USD, EUR/USD, AUD/USD, USD/CHF and USD/JPY pairs only and target anywhere between 25-50 pips a day with a risk/reward ratio of at least 2:1.</p>
  <p>Our maximum drawdown is 10% and we strive to average 150-250 pips per month. We strongly recommend no more than 3% leveraged risk of your account for any trade. Most trades are closed within hours.</p>
  <div class="cta"><span class="btn">Learn More About Forex Basics!</span></div>
</section>

<section class="why">
  <h2 class="section-title on-dark">WHY TRADLO</h2>
  <div class="why-art" role="img" aria-label="Round green diagram of service icons around a dark central disc"></div>
  <div class="point center" style="top:102px">Our objective is to provide global access to trusted forex signals.</div>
  <div class="point left" style="left:80px;top:236px">Our motto is to 'Change Your World' and also to ensure that you earn profits on a regular basis.</div>
  <div class="point" style="left:870px;top:236px">Our services are highly affordable.</div>
  <div class="point left" style="left:80px;top:400px">We're a highly dependable and trusted forex trading platform.</div>
  <div class="point" style="left:870px;top:400px">We offer High Probable forex strategies with high rewards.</div>
  <div class="point left" style="left:80px;top:560px">We offer speedy, consistent, accurate and desired results.</div>
  <div class="point" style="left:870px;top:560px">We set transparent entry price and exit levels.</div>
  <div class="point center" style="top:652px">Our team will constantly update you regarding the status of your trade till the time it is closed.</div>
</section>

<section class="performance">
  <h2 class="section-title">PERFORMANCE</h2>
  <div class="year-select">2017 <svg width="12" height="8"><path d="M1 1l5 5 5-5" fill="none" stroke="#333" stroke-width="2"/></svg></div>
  <div class="tables">
    <table class="pips-table">
      <tr><th>Month</th><th>PIPS</th></tr>
      <tr><td>January</td><td></td></tr><tr><td>February</td><td></td></tr><tr><td>March</td><td></td></tr>
      <tr><td>April</td><td></td></tr><tr><td>May</td><td></td></tr><tr><td>June</td><td></td></tr>
    </table>
    <table class="pips-table">
      <tr><th>Month</th><th>PIPS</th></tr>
      <tr><td>July</td><td></td></tr><tr><td>August</td><td></td></tr><tr><td>September</td><td></td></tr>
      <tr><td>October</td><td></td></tr><tr><td>November</td><td></td></tr><tr><td>December</td><td></td></tr>
    </table>
  </div>
</section>

<section class="membership">
  <div class="membership-art" role="img" aria-label="Softly blurred office scene in green tones"></div>
  <h2 class="section-title on-dark">MEMBERSHIP</h2>
  <div class="plans">
    <div class="plan">
      <div class="price">Free</div><div class="period">1 MONTH</div>
      <ul><li>Lorem ipsum</li><li>Dolor sit amet</li><li>Adipiscing elit</li><li>Euismod tincidunt</li><li>Duis autem vel eum iriure</li></ul>
      <div class="order">ORDER NOW</div>
    </div>
    <div class="plan">
      <div class="price">$ 139</div><div class="period">3 MONTHS</div>
      <ul><li>Lorem ipsum</li><li>Dolor sit amet</li><li>Adipiscing elit</li><li>Euismod tincidunt</li><li>Duis autem vel eum iriure</li></ul>
      <div class="order">ORDER NOW</div>
    </div>
  </div>
</section>

<section class="faq">
  <h2>FREQUENTLY ASKED <span>QUESTIONS</span></h2>
  <div class="faq-grid">
    <div>+ Why Tradlo?</div><div>+ Can I follow your signals if I have a full-time job?</div>
    <div>+ What is your trading philosophy and style?</div><div>+ How will I know when a new signal is released?</div>
    <div>+ How many signals do you send out per month?</div><div>+ How do I subscribe to your service?</div>
    <div>+ How many pips can I make per month following your signals?</div><div>+ What happens after my 30-day free trial access?</div>
  </div>
</section>

<section class="contact">
  <div class="message-form">
    <h2>SEND <span>A MESSAGE</span></h2>
    <div class="form-grid">
      <div class="field">Name</div><div class="field">Email Address</div>
      <div class="field">Phone Number</div><div class="field">Company</div>
      <div class="field message">Message</div>
    </div>
  </div>
  <div class="contact-info">
    <h2>CONTACT <span>INFO</span></h2>
    <ul>
      <li><span class="bullet"></span><span><strong>TRADLO</strong><br>1234 Lorem Ipsum Dr<br>Ste 200<br>Ridgewater, Alberta</span></li>
      <li><span class="bullet"></span><span>(800) 555-0142</span></li>
      <li><span class="bullet"></span><span>info@tradlo.example</span></li>
    </ul>
  </div>
</section>

<section class="trial">
  <span class="seal"></span>
  <p>Free forex signals for 30 days. Start your trial right now.</p>
  <span class="btn-trial">START FREE TRIAL</span>
</section>

<section class="disclaimer">
  <p>Disclaimer: Trading foreign exchange ("Forex") on margin carries a high level of risk and may not be suitable for all investors. Before deciding to trade Forex you should carefully consider your investment objectives, level of experience and appetite for risk. You could lose some or all of your initial deposit, so never trade with money you cannot afford to lose. Past performance shown on this site is not a guarantee of future results. Tradlo offers signals for educational purposes only and does not give personal financial advice. Please seek guidance from an independent advisor if you have any doubts. By using this service you accept that all trading decisions remain your own responsibility. All information provided by Tradlo is for educational purposes only.</p>
</section>

<footer class="site-footer">
  <span>© 2017 TRADLO | All rights reserved |</span>
  <nav><span>About the Founder</span><span>Personal Development Resources</span><span>Forex Resources</span><span>Terms of Service</span></nav>
</footer>

</body>
</html>
```